Web design project for exciting Australian start-up

Background
We are looking for a creative and talented web design artist to work alongside our market leading web developer.
• You will be required to create a modern and clean design theme for our website, incorporating selected rustic colour scheme elements for our exciting Australian start-up to operate within the coffee industry.
reoccurring work to be expected to flow to the successful designer.
Requirements
• c. 5 - 10 page website
• Landing page
• Log in/ out
• 404 template
• Typography is emphasised
• Please use either a) typemarrow.com, b) free web fonts, c) brindle fonts
• All design elements in vector format
• Preferably with icons for each header title(i.e. about us, how it works etc) but designer have free reign over how the site looks, so might not be applicable
• All pages to be responsive
• Down to eSlab resolution

High level visual design brief attached - additional pages to be worked from base design.

Design inspiration
• We would like to use design elements from the following sources:
http://www.zandrix.com/halcyon/ (Functionality)
Colour scheme refer to logo and complementary style guide

```html
<!DOCTYPE html>
<html lang="en">
<head>
<meta charset="utf-8">
<title>Bean Harbor — Online Coffee Marketplace</title>
<link rel="stylesheet" href="https://fonts.googleapis.com/css2?family=Open+Sans:wght@300;400;600;700&display=swap">
<style>
  :root {
    --orange: #f0982a;
    --orange-dark: #e07f12;
    --ink: #222222;
    --text: #555555;
    --cream: #fbf3e4;
    --cream-edge: #f6ead3;
    --footer-link: #3f3f3f;
    --copyright: #b8803a;
    --white: #ffffff;
  }
  * { box-sizing: border-box; margin: 0; padding: 0; }
  html, body { width: 1158px; height: 1200px; overflow: hidden; background: var(--white); }
  body { position: relative; font-family: "Open Sans", Arial, sans-serif; color: var(--text); }

  .top-band { position: absolute; left: 0; top: 0; width: 100%; height: 6px; background: var(--orange); }

  .brand { position: absolute; left: 97px; top: 44px; display: flex; align-items: center; gap: 12px; }
  .brand-dot { width: 58px; height: 58px; border-radius: 50%; background: var(--orange); }
  .brand-name { font-weight: 700; font-size: 32px; letter-spacing: 1px; color: var(--ink); }

  .account { position: absolute; top: 67px; right: 92px; display: flex; gap: 7px; }
  .btn { display: block; width: 101px; height: 35px; line-height: 35px; text-align: center; font-size: 14px; text-decoration: none; color: var(--white); }
  .btn-login { background: linear-gradient(#f5a93c, var(--orange-dark)); }
  .btn-signup { background: linear-gradient(#333, #111); }

  .hero { position: absolute; left: 97px; top: 134px; width: 970px; height: 444px; overflow: hidden; }
  .hero-photo { position: absolute; inset: 0;
    background: linear-gradient(100deg, #7a3f14 0%, #b0652a 28%, #d89a55 48%, #9a6a3e 68%, #5a2f12 100%); }
  .hero-frame { position: absolute; border: 2px solid rgba(255,255,255,.55); }
  .hero-frame.outer { left: 9px; top: 12px; right: 9px; bottom: 12px; }
  .hero-frame.inner { left: 19px; top: 20px; right: 19px; bottom: 20px; border-width: 1px; }
  .hero-copy { position: absolute; left: 62px; top: 96px; color: var(--white); font-weight: 300; }
  .hero-line-1 { font-size: 47px; line-height: 1; margin-left: 6px; }
  .hero-line-2 { font-size: 69px; line-height: 1; margin-top: 8px; margin-left: -2px; }
  .hero-line-3 { font-size: 43px; line-height: 1; margin-top: 9px; margin-left: 8px; }
  .watch-btn { position: absolute; left: 65px; top: 293px; width: 181px; height: 44px; border: 2px solid var(--white);
    background: linear-gradient(#f5a43a, var(--orange-dark)); color: var(--white); font-weight: 600; font-size: 18px;
    display: flex; align-items: center; justify-content: center; gap: 8px; text-decoration: none; }

  .feature { position: absolute; top: 612px; }
  .feature h2 { font-weight: 300; font-size: 27px; color: #333; line-height: 1; }
  .about { left: 97px; width: 330px; }
  .about h2 { color: var(--orange); font-size: 35px; }
  .about p { font-size: 12px; line-height: 21px; margin-top: 9px; }
  .about p + p { margin-top: 6px; }
  .special { left: 450px; top: 621px; width: 295px; }
  .works { left: 768px; top: 621px; width: 295px; }
  .feature-photo { width: 286px; height: 101px; margin-top: 12px; }
  .photo-coffee { background: linear-gradient(90deg, #4a2a18, #7a4a2a 45%, #c9a47a 75%, #b08a60); }
  .photo-cups { background: linear-gradient(90deg, #3a3633, #8a847c 40%, #bdb7ae 60%, #3f3a36); }
  .feature h3 { font-weight: 400; font-size: 16px; color: #555; margin: 10px 0 0 3px; }
  .feature .caption { font-size: 12px; line-height: 21px; margin: 2px 0 0 3px; }

  .footer { position: absolute; left: 0; top: 893px; width: 100%; height: 250px; background: var(--cream); border-top: 4px solid var(--cream-edge); }
  .footer-col { position: absolute; top: 31px; width: 230px; }
  .footer-col:nth-child(1) { left: 98px; }
  .footer-col:nth-child(2) { left: 353px; }
  .footer-col:nth-child(3) { left: 612px; }
  .ribbon { height: 37px; line-height: 37px; padding-left: 22px; color: var(--white); font-size: 17px; background: var(--orange);
    clip-path: polygon(0 0, 92% 0, 100% 50%, 92% 100%, 0 100%); }
  .footer-col ul { list-style: none; margin: 7px 0 0 22px; }
  .footer-col li { font-size: 13px; color: var(--footer-link); line-height: 26.5px; display: flex; align-items: center; gap: 7px; }
  .social-box { width: 18px; height: 18px; background: #3d6db1; display: inline-block; }
  .social-box.chirp { background: #4ab3e6; }
  .social-box.link { background: #1d6ea8; }
  .social-box.vid { background: #c4302b; }

  .copyright { position: absolute; left: 108px; top: 1164px; font-size: 11.5px; color: var(--copyright); }
</style>
</head>
<body>
  <div class="top-band"></div>

  <header>
    <div class="brand">
      <span class="brand-dot"></span>
      <span class="brand-name">BEAN HARBOR</span>
    </div>
    <nav class="account">
      <a class="btn btn-login" href="#">LOGIN</a>
      <a class="btn btn-signup" href="#">SIGN UP</a>
    </nav>
  </header>

  <section class="hero">
    <div class="hero-photo" role="img" aria-label="Coffee beans spilling from a burlap sack beside cinnamon sticks and a steaming white cup on a wooden table"></div>
    <div class="hero-frame outer"></div>
    <div class="hero-frame inner"></div>
    <div class="hero-copy">
      <div class="hero-line-1">Australia’a first</div>
      <div class="hero-line-2">Online Coffee</div>
      <div class="hero-line-3">Marketplace</div>
    </div>
    <a class="watch-btn" href="#">
      <svg width="10" height="16" viewBox="0 0 10 16"><path d="M2 2l6 6-6 6" fill="none" stroke="#fff" stroke-width="2"/></svg>
      WATCH VIDEO
    </a>
  </section>

  <section class="feature about">
    <h2>About Our Shop</h2>
    <p>Etiam eu urna Sed porta Suspendisse quam leo molestie sed luctus quis feugiat in pede Fusce tellus Sed metus augue convallis et vehicula ut pulvinar eu ante Integer orci tellus tristique vitae consequat nec</p>
    <p>Etiam eu urna Sed porta Suspendisse quam leo molestie sed luctus quis feugiat in pede Fusce tellus Sed metus augue convallis et vehicula ut pulvinar eu ante Integer orci tellus tristique vitae consequat nec</p>
  </section>

  <section class="feature special">
    <h2>Special Coffee</h2>
    <div class="feature-photo photo-coffee" role="img" aria-label="Latte with heart art beside roasted coffee beans"></div>
    <h3>Susce tellus Sed metus augue</h3>
    <p class="caption">convallis et vehicula ut pulvinar eu ante Integer orci tellus tristique vitae consequat nec porta vel</p>
  </section>

  <section class="feature works">
    <h2>How it Works</h2>
    <div class="feature-photo photo-cups" role="img" aria-label="Hands holding a tray with two takeaway coffee cups"></div>
    <h3>Susce tellus Sed metus augue</h3>
    <p class="caption">convallis et vehicula ut pulvinar eu ante Integer orci tellus tristique vitae consequat nec porta vel</p>
  </section>

  <footer class="footer">
    <div class="footer-col">
      <div class="ribbon">Helpful Information</div>
      <ul>
        <li>About us</li>
        <li>Media enquiries</li>
        <li>Terms &amp; conditions</li>
        <li>Privacy policy</li>
      </ul>
    </div>
    <div class="footer-col">
      <div class="ribbon">Who we are</div>
      <ul>
        <li>How it works</li>
        <li>FAQ</li>
        <li>Contact us</li>
      </ul>
    </div>
    <div class="footer-col">
      <div class="ribbon">Join Us Now</div>
      <ul>
        <li><span class="social-box"></span>Friendwall</li>
        <li><span class="social-box chirp"></span>Chirpline</li>
        <li><span class="social-box link"></span>Linkboard</li>
        <li><span class="social-box vid"></span>Vidstream</li>
      </ul>
    </div>
  </footer>

  <p class="copyright">© 2014 Company Name&nbsp; All right reserved&nbsp; Term of Use</p>
</body>
</html>
```